High-Converting Facebook Ads for Portals Drapes & Louvres (6 Products)

We are looking for a graphic designer to create high-quality Facebook & Instagram ads for our business: Portals Drapes and Louvres (Melbourne, Australia).

We require 6 separate ad designs, each for a different product:

Zipscreen Blinds

Outdoor Awnings

Plantation Shutters

Roller Shutters

Security Doors

Roller Blinds & Sheer Curtains

Ad Specifications:

Sizes:

1440 x 1800 px (4:5 ratio)

1080 x 1080 px (1:1 ratio)

1080 x 1920 px (9:16 ratio for Stories/Reels)

Format: PNG (high resolution, not blurry)

Designed specifically for Meta (Facebook/Instagram ads)

Mobile-friendly layout (clear, easy to read)

Style:

Bold, sales-driven, retail-style ads (NOT minimal)

Eye-catching and designed to generate leads

Clean, professional layout

Similar to promotional home improvement ads

Brand Colours:

Red: #E31E24

Blue: #0072BC

White backgrounds

Each ad must include:

“SALE NOW ON” banner at top

Our showroom address:
482 Upper Wattleby Road, Kestrel Heights (must be fully visible, not cut off)

Phone number: 9471 2658

Our logo (provided)

Badge: “Celebrating 13 YEARS in Business” (must be clean and readable)

Call to Action:

For 5 ads: “Book a FREE quote TODAY!”

For Security Doors ad: “ORDER NOW”

Offers / Pricing:

Most products: “UP TO 40% OFF”

Plantation Shutters: “FROM $299/sqm”

Security Doors: “FROM $750”

Content for each ad (examples):

Zipscreen Blinds:

Made to Measure

Fully Installed

Wind, Sun & Insect Protection

Outdoor Awnings:

Reduce Heat & Glare

Energy Saving

Custom Made

Plantation Shutters:

Modern & Elegant

Light & Privacy Control

Durable & Easy Care

Roller Shutters:

Security Protection

Block Heat & Noise

Total Light Control

Security Doors:

3 Point Locking

Premium Mesh

Custom Made

Blinds & Sheers:

Huge Range of Fabrics

Modern Soft Finish

Perfect for Any Room

Important Notes:

All text must be sharp and easy to read (no blur)

Layout must be balanced and not overcrowded

Ensure no text is cut off (especially address and headings)

Badge text must be straight and professional (no distortion)

Use high-quality, relevant images (we will provide references)

Goal:
Create ads that look professional, trustworthy, and generate enquiries/bookings for in-home quotes.

We are open to creative ideas but want a strong, bold retail-style ad that converts.
I have uploaed chatgpt mocks

Target Market(s)

Homeowners in Melbourne, Australia (typically aged 30–65) looking to improve their homes with blinds, shutters, awnings and security doors. Mid to high income households focused on quality, security, and modern home upgrades.

Industry/Entity Type

Home Improvement / Construction / Retail

Font styles to use
Sans Serif

Requirements
Must have
• Clear, bold and easy-to-read text (must be readable on mobile) High-quality, non-blurry design Strong “SALE” style layout (retail promotional look) Proper spacing (no overcrowded designs) All key info visible (address must NOT be cut off) Correct pricing and offers included Clean “13 YEARS” badge (no distortion or curved text) Consistent branding across all 6 ads
Nice to have
• Modern, slightly premium feel while still being bold Good use of contrast (red/blue/white) Subtle shadows or layering to improve depth Clean use of icons or bullet points Strong hierarchy (headline → benefits → offer → CTA) Variations in layout for testing different ad styles
Should not have
• Minimal or plain designs (we want bold, sales-driven ads) Hard-to-read fonts or script fonts Low-quality or blurry images Overcrowded layouts with too much text Important text cut off (especially address or headings) Overuse of effects or “cheap” looking graphics Yellow-heavy colour schemes (must follow brand colours)

```html
<!DOCTYPE html>
<html lang="en">
<head>
<meta charset="utf-8">
<title>Portals Drapes and Louvres – Sale Ads 4:5</title>
<link href="https://fonts.googleapis.com/css2?family=Anton&family=Bebas+Neue&family=Lexend:wght@400;500;600&display=swap" rel="stylesheet">
<style>
  :root{
    --red:#E31E24;
    --blue:#0072BC;
    --white:#ffffff;
    --ink:#14213d;
    --stage:#000000;
    --title:#444444;
    --badge:#e9eef4;
  }
  *{box-sizing:border-box;margin:0;padding:0}
  html,body{width:1200px;height:1200px;overflow:hidden;background:var(--stage)}
  .board{position:relative;width:1200px;height:1200px}
  .board-title{
    position:absolute;top:150px;left:0;width:1200px;text-align:center;
    font-family:"Anton",sans-serif;font-size:56px;line-height:1.2;color:var(--title);letter-spacing:1px;font-weight:400;
  }
  .ad{position:absolute;width:286px;height:357px;background:var(--white);overflow:hidden}
  .ad--1{left:152px;top:283px}.ad--2{left:454px;top:283px}.ad--3{left:756px;top:283px}
  .ad--4{left:152px;top:654px}.ad--5{left:454px;top:654px}.ad--6{left:761px;top:654px}

  .ad-header{position:absolute;left:0;top:0;width:100%;height:75px;background:var(--blue)}
  .badge{position:absolute;left:6px;top:7px;width:60px;height:60px;border-radius:50%;background:var(--badge)}
  .sale-headline{
    position:absolute;left:76px;top:12px;font-weight:400;
    font-family:"Bebas Neue",sans-serif;font-size:51px;line-height:1;color:var(--white);
    letter-spacing:-0.5px;white-space:nowrap;
  }
  .cta{
    position:absolute;left:0;width:100%;top:83px;text-align:center;
    font-family:"Anton",sans-serif;font-size:22px;line-height:1;color:var(--red);letter-spacing:.6px;
  }
  .offer{
    position:absolute;left:0;width:100%;top:105px;text-align:center;
    font-family:"Anton",sans-serif;font-size:40px;line-height:1;color:var(--blue);letter-spacing:1.5px;
  }
  .offer--price{font-size:36px;top:107px;letter-spacing:.5px}
  .cta--order{top:78px;font-size:50px;letter-spacing:1.5px}
  .offer--from{top:124px;font-size:48px;letter-spacing:1px}

  .category{
    position:absolute;left:0;top:168px;height:27px;padding:0 16px 0 12px;
    background:var(--red);border-radius:0 14px 14px 0;
    font-family:"Anton",sans-serif;font-size:10.5px;line-height:27px;color:var(--white);letter-spacing:.4px;
  }
  .benefits{position:absolute;left:10px;top:208px;width:116px;list-style:none;
    font-family:"Lexend",sans-serif;font-weight:500;font-size:10px;line-height:1.25;color:var(--ink)}
  .benefits li{position:relative;padding-left:10px;margin-bottom:6px}
  .benefits li::before{
    content:"";position:absolute;left:1px;top:4px;width:4px;height:4px;background:var(--blue);transform:rotate(45deg);
  }
  .photo-frame{position:absolute;left:128px;top:146px;width:146px;height:146px;
    background:var(--red);border-radius:47% 53% 50% 50% / 52% 46% 54% 48%}
  .photo{position:absolute;inset:5px;border-radius:50% 46% 52% 48% / 47% 52% 48% 53%}
  .photo--zip{background:linear-gradient(160deg,#7c8a8e,#b9bdb6 45%,#4f8a3a)}
  .photo--awning{background:linear-gradient(170deg,#3b3b3d,#8fb0c9 35%,#6f9460 60%,#a39b8c)}
  .photo--plantation{background:linear-gradient(100deg,#6e7378,#e6e8ea 40%,#c9cdd1 75%,#5d6166)}
  .photo--roller{background:linear-gradient(160deg,#3c3d40,#5c5e62 45%,#a8876a 80%,#d9d9d6)}
  .photo--door{background:linear-gradient(100deg,#d8d6d2,#5a5e63 35%,#3a3d41 65%,#cfcdc8)}
  .photo--sheer{background:linear-gradient(170deg,#e9eef3,#8d8f93 40%,#6f7176 70%,#d8b5a6)}

  .ad-footer{position:absolute;left:0;bottom:0;width:100%;height:54px;background:var(--blue);color:var(--white)}
  .phone-row{position:absolute;left:10px;top:5px;display:flex;align-items:center;gap:7px}
  .phone-number{font-family:"Anton",sans-serif;font-size:28px;line-height:1;letter-spacing:2.5px}
  .address-row{position:absolute;left:10px;top:37px;display:flex;align-items:center;gap:6px;
    font-family:"Lexend",sans-serif;font-size:7.5px;white-space:nowrap}
  .brand-name{position:absolute;right:10px;top:10px;width:74px;text-align:center;
    font-family:"Lexend",sans-serif;font-weight:600;font-size:9px;line-height:1.15;color:var(--white)}
  .brand-name::before{content:"";display:block;width:12px;height:12px;margin:0 auto 3px;background:var(--white)}
</style>
</head>
<body>
<main class="board">
  <h1 class="board-title">1440 x 1800 px (4:5 ratio)</h1>

  <svg width="0" height="0" style="position:absolute">
    <defs>
      <symbol id="icon-phone" viewBox="0 0 24 24"><circle cx="12" cy="12" r="11" fill="#fff"/><path d="M8 6.5l2 2.2-1 1.6c.8 1.7 2 2.9 3.7 3.7l1.6-1 2.2 2-1 2c-4.6-.3-8.5-4.2-8.8-8.8z" fill="#0072BC"/></symbol>
      <symbol id="icon-pin" viewBox="0 0 24 24"><path d="M12 2a7 7 0 0 0-7 7c0 5 7 13 7 13s7-8 7-13a7 7 0 0 0-7-7z" fill="#fff"/><circle cx="12" cy="9" r="2.6" fill="#0072BC"/></symbol>
    </defs>
  </svg>

  <article class="ad ad--1">
    <header class="ad-header"><div class="badge" role="img" aria-label="Anniversary badge"></div><h2 class="sale-headline">SALE NOW ON</h2></header>
    <p class="cta">BOOK A FREE QUOTE TODAY!</p>
    <p class="offer">UP TO 40% OFF</p>
    <span class="category">ZIPSCREEN BLINDS</span>
    <ul class="benefits"><li>Made to Measure</li><li>Fully Installed</li><li>Wind, Sun &amp; Insect Protection</li></ul>
    <div class="photo-frame"><div class="photo photo--zip" role="img" aria-label="Patio enclosed with zipscreen blinds"></div></div>
    <footer class="ad-footer">
      <div class="phone-row"><svg width="12" height="12"><use href="#icon-phone"/></svg><span class="phone-number">9471 2658</span></div>
      <div class="address-row"><svg width="11" height="11"><use href="#icon-pin"/></svg>482 Upper Wattleby Road, Kestrel Heights</div>
      <div class="brand-name">Portals Drapes and Louvres</div>
    </footer>
  </article>

  <article class="ad ad--2">
    <header class="ad-header"><div class="badge" role="img" aria-label="Anniversary badge"></div><h2 class="sale-headline">SALE NOW ON</h2></header>
    <p class="cta">BOOK A FREE QUOTE TODAY!</p>
    <p class="offer">UP TO 40% OFF</p>
    <span class="category" style="top:178px">OUTDOOR AWNINGS</span>
    <ul class="benefits" style="top:218px"><li>Reduce Heat &amp; Glare</li><li>Energy Saving</li><li>Custom Made</li></ul>
    <div class="photo-frame" style="left:130px"><div class="photo photo--awning" role="img" aria-label="Folding arm awning over an outdoor deck"></div></div>
    <footer class="ad-footer">
      <div class="phone-row"><svg width="12" height="12"><use href="#icon-phone"/></svg><span class="phone-number">9471 2658</span></div>
      <div class="address-row"><svg width="11" height="11"><use href="#icon-pin"/></svg>482 Upper Wattleby Road, Kestrel Heights</div>
      <div class="brand-name">Portals Drapes and Louvres</div>
    </footer>
  </article>

  <article class="ad ad--3">
    <header class="ad-header"><div class="badge" role="img" aria-label="Anniversary badge"></div><h2 class="sale-headline">SALE NOW ON</h2></header>
    <p class="cta">BOOK A FREE QUOTE TODAY!</p>
    <p class="offer offer--price">FROM $299/sqm</p>
    <span class="category" style="top:170px">PLANTATION SHUTTERS</span>
    <ul class="benefits" style="top:210px"><li>Modern &amp; Elegant</li><li>Light &amp; Privacy Control</li><li>Durable &amp; Easy Care</li></ul>
    <div class="photo-frame" style="top:150px"><div class="photo photo--plantation" role="img" aria-label="White plantation shutters on a window"></div></div>
    <footer class="ad-footer">
      <div class="phone-row"><svg width="12" height="12"><use href="#icon-phone"/></svg><span class="phone-number">9471 2658</span></div>
      <div class="address-row"><svg width="11" height="11"><use href="#icon-pin"/></svg>482 Upper Wattleby Road, Kestrel Heights</div>
      <div class="brand-name">Portals Drapes and Louvres</div>
    </footer>
  </article>

  <article class="ad ad--4">
    <header class="ad-header"><div class="badge" role="img" aria-label="Anniversary badge"></div><h2 class="sale-headline">SALE NOW ON</h2></header>
    <p class="cta">BOOK A FREE QUOTE TODAY!</p>
    <p class="offer">UP TO 40% OFF</p>
    <span class="category">ROLLER SHUTTERS</span>
    <ul class="benefits"><li>Security Protection</li><li>Block Heat &amp; Noise</li><li>Total Light Control</li></ul>
    <div class="photo-frame"><div class="photo photo--roller" role="img" aria-label="Dark roller shutter on a brick home window"></div></div>
    <footer class="ad-footer">
      <div class="phone-row"><svg width="12" height="12"><use href="#icon-phone"/></svg><span class="phone-number">9471 2658</span></div>
      <div class="address-row"><svg width="11" height="11"><use href="#icon-pin"/></svg>482 Upper Wattleby Road, Kestrel Heights</div>
      <div class="brand-name">Portals Drapes and Louvres</div>
    </footer>
  </article>

  <article class="ad ad--5">
    <header class="ad-header"><div class="badge" role="img" aria-label="Anniversary badge"></div><h2 class="sale-headline">SALE NOW ON</h2></header>
    <p class="cta cta--order">ORDER NOW</p>
    <p class="offer offer--from">FROM $750</p>
    <span class="category" style="top:190px">SECURITY DOORS</span>
    <ul class="benefits" style="top:229px"><li>3 Point Locking</li><li>Premium Mesh</li><li>Custom Made</li></ul>
    <div class="photo-frame" style="left:139px;top:170px;width:132px;height:132px"><div class="photo photo--door" role="img" aria-label="Dark framed security door at a front entry"></div></div>
    <footer class="ad-footer">
      <div class="phone-row"><svg width="12" height="12"><use href="#icon-phone"/></svg><span class="phone-number">9471 2658</span></div>
      <div class="address-row"><svg width="11" height="11"><use href="#icon-pin"/></svg>482 Upper Wattleby Road, Kestrel Heights</div>
      <div class="brand-name">Portals Drapes and Louvres</div>
    </footer>
  </article>

  <article class="ad ad--6">
    <header class="ad-header"><div class="badge" role="img" aria-label="Anniversary badge"></div><h2 class="sale-headline">SALE NOW ON</h2></header>
    <p class="cta">BOOK A FREE QUOTE TODAY!</p>
    <p class="offer">UP TO 40% OFF</p>
    <span class="category">BLINDS &amp; SHEERS</span>
    <ul class="benefits" style="left:10px;top:210px;width:112px"><li>Huge Range of Fabrics</li><li>Modern Soft Finish</li><li>Perfect for Any Room</li></ul>
    <div class="photo-frame"><div class="photo photo--sheer" role="img" aria-label="Bedroom with grey curtains and sheers"></div></div>
    <footer class="ad-footer">
      <div class="phone-row"><svg width="12" height="12"><use href="#icon-phone"/></svg><span class="phone-number">9471 2658</span></div>
      <div class="address-row"><svg width="11" height="11"><use href="#icon-pin"/></svg>482 Upper Wattleby Road, Kestrel Heights</div>
      <div class="brand-name">Portals Drapes and Louvres</div>
    </footer>
  </article>
</main>
</body>
</html>
```